Fresh, modern, fun business card for pediatric dental practice

Need a business card for fresh, modern, fun pediatric dental practice

Clean look that matches our website's font and colors

We prefer the look of curved corners on business cards

Target Market(s)

parents (mothers) of young children, professionals, mid-high class

Industry/Entity Type

Dental

Contact Information for Business Card

Maplebrook Pediatric Dentistry
482 Quarry Lane
Suite 517
Fernwick, PA 17590
717.555.0193
www.maplebrookkidsdental.example

Mei-Ran Tsai, DMD
Corinne Walbeck, DMD
(we are working on our email address, but we would like that on the card as well)

Font styles to use
Sans Serif

Requirements
Must have
• All info; we would also like to make cards for individual staff members
• colors from our website and color palatte, attatched
• use same font and design as website for branding
Nice to have
• clean, simple card that has a pop of color
• we would like to see a few designs with our tag line "where smiles get brighter"
• we are not sure if we want to have it on there or not
• we would like to see a few designs incorporating the ribbon graphic on our website where the word WELCOME is

```html
<!DOCTYPE html>
<html lang="en">
<head>
<meta charset="utf-8">
<title>Maplebrook Pediatric Dentistry – Business Card</title>
<link rel="stylesheet" href="https://fonts.googleapis.com/css2?family=Open+Sans:wght@400;600&family=Raleway:wght@500&display=swap">
<style>
  :root {
    --stage: #000000;
    --card: #ffffff;
    --magenta: #c81f80;
    --gold: #eba91c;
    --sun: #f5b823;
  }
  html, body {
    margin: 0;
    width: 1200px;
    height: 900px;
    overflow: hidden;
    background: var(--stage);
  }
  .canvas {
    position: relative;
    width: 1200px;
    height: 900px;
  }
  .card {
    position: absolute;
    top: 271px;
    width: 457px;
    height: 282px;
    background: var(--card);
    border-radius: 14px;
    overflow: hidden;
  }
  .card--front { left: 137px; }
  .card--back { left: 626px; }

  .doctors {
    position: absolute;
    left: 31px;
    top: 34px;
    margin: 0;
    font-family: "Raleway", sans-serif;
    font-weight: 500;
    font-size: 18px;
    line-height: 20px;
    color: var(--magenta);
  }
  .doctors .surname { color: var(--gold); }
  .doctors .degree { font-size: 13px; color: var(--gold); }

  .practice {
    position: absolute;
    left: 31px;
    top: 94px;
    font-family: "Open Sans", sans-serif;
    font-size: 12.5px;
    line-height: 19px;
    color: var(--magenta);
  }
  .practice-name {
    margin: 0;
    font-weight: 600;
    font-size: 14px;
    color: var(--gold);
  }
  .practice-address { margin: 0; font-style: normal; }

  .contacts {
    position: absolute;
    left: 31px;
    top: 168px;
    margin: 0;
    padding: 0;
    list-style: none;
    font-family: "Open Sans", sans-serif;
    font-size: 12.5px;
    line-height: 19px;
    color: var(--magenta);
  }
  .contacts li {
    display: flex;
    align-items: center;
    gap: 11px;
  }
  .contacts svg {
    width: 11px;
    height: 11px;
    fill: var(--gold);
    flex: none;
  }

  .brand {
    position: absolute;
    left: 170px;
    top: 119px;
    width: 250px;
    text-align: center;
    font-family: "Open Sans", sans-serif;
    font-weight: 600;
    color: var(--gold);
  }
  .brand-dot {
    display: block;
    width: 30px;
    height: 30px;
    margin: 0 auto 22px;
    border-radius: 50%;
    background: var(--sun);
  }
  .brand-name {
    margin: 0;
    font-size: 38px;
    line-height: 40px;
    letter-spacing: 1px;
  }
  .brand-tag {
    margin: 0;
    font-size: 20px;
    line-height: 26px;
    letter-spacing: 2.4px;
  }
</style>
</head>
<body>
<main class="canvas">
  <section class="card card--front" aria-label="Card front">
    <h1 class="doctors">
      Mei-Ran <span class="surname">Tsai,</span> <span class="degree">DMD</span><br>
      Corinne <span class="surname">Walbeck,</span> <span class="degree">DMD</span>
    </h1>
    <div class="practice">
      <p class="practice-name">Maplebrook Pediatric Dentistry</p>
      <address class="practice-address">482 Quarry Lane&nbsp; Suite<br>517 Fernwick, PA 17590</address>
    </div>
    <ul class="contacts">
      <li>
        <svg viewBox="0 0 12 12" aria-hidden="true"><path d="M2.4 0.6 4.3 2.8 3.4 4.3C4 5.7 6.2 8 7.7 8.6L9.2 7.7 11.4 9.6 10.3 11.3C5.6 11.6 0.4 6.4 0.7 1.7Z"/></svg>
        <span>717.555.0193</span>
      </li>
      <li>
        <svg viewBox="0 0 12 12" aria-hidden="true"><path d="M0.5 2.5H11.5V3.3L6 6.6 0.5 3.3ZM0.5 4.4 6 7.7 11.5 4.4V9.5H0.5Z"/></svg>
        <span>Mei-ran@maplebrookkidsdental.example</span>
      </li>
      <li>
        <svg viewBox="0 0 12 12" aria-hidden="true"><path d="M0.5 2.5H11.5V3.3L6 6.6 0.5 3.3ZM0.5 4.4 6 7.7 11.5 4.4V9.5H0.5Z"/></svg>
        <span>Corinne@maplebrookkidsdental.example</span>
      </li>
      <li>
        <svg viewBox="0 0 12 12" aria-hidden="true"><circle cx="6" cy="6" r="5.5"/></svg>
        <span>www.maplebrookkidsdental.example</span>
      </li>
    </ul>
  </section>

  <section class="card card--back" aria-label="Card back">
    <div class="brand">
      <span class="brand-dot" aria-hidden="true"></span>
      <p class="brand-name">maplebrook</p>
      <p class="brand-tag">pediatric dentistry</p>
    </div>
  </section>
</main>
</body>
</html>
```